Northfield Builders Guild Business card

We are looking for a new business card design with photo included.
Our business is a nonprofit construction contractor membership organization. We offer business education, assist with business setup and licensing, provide safety training, and provide a member directory.
URL: www.builderslinkguild.org
Color code:
CMYK: 0 cyan, 42 magenta, 100 yellow, 0 black for Print.
Hexidecimal: #FF9900
RGB: R 255; G 153; B 0

```html
<!DOCTYPE html>
<html lang="en">
<head>
<meta charset="UTF-8">
<title>Northfield Builders Guild — Business Card</title>
<link rel="stylesheet" href="https://fonts.googleapis.com/css2?family=Montserrat:wght@500;600;800&display=swap">
<style>
  :root {
    --bg: #e4e4e4;
    --orange: #ff9900;
    --card-orange: #f7951f;
    --charcoal: #3a393a;
    --charcoal-deep: #2f2e2f;
    --white: #ffffff;
    --ink: #333233;
  }
  * { box-sizing: border-box; margin: 0; padding: 0; }
  html, body { width: 1200px; height: 1200px; overflow: hidden; background: var(--bg); }
  body { font-family: 'Montserrat', sans-serif; position: relative; }

  .card {
    position: absolute;
    left: 200px;
    width: 800px;
    height: 457px;
    border-radius: 24px;
    overflow: hidden;
  }
  .card--front { top: 150px; display: flex; }
  .card--back { top: 700px; background: var(--card-orange); }

  .front__brand {
    width: 410px;
    background: var(--white);
    display: flex;
    align-items: center;
    justify-content: center;
  }
  .front__divider { width: 6px; background: var(--charcoal); position: relative; }
  .front__divider::after {
    content: ""; position: absolute; left: 1px; top: 0; bottom: 0; width: 3px; background: var(--orange);
  }
  .front__details {
    flex: 1;
    background: linear-gradient(180deg, var(--charcoal) 0%, var(--charcoal-deep) 100%);
    padding: 102px 0 0 32px;
    color: var(--white);
  }

  .wordmark {
    font-weight: 800;
    text-align: center;
    line-height: 1.05;
    letter-spacing: 0.5px;
  }
  .wordmark--front { color: var(--ink); font-size: 34px; }
  .wordmark--back { color: var(--ink); font-size: 52px; }

  .contact__name { color: var(--orange); font-weight: 600; font-size: 27px; letter-spacing: 0.3px; }
  .contact__title { font-weight: 500; font-size: 18px; margin-top: 1px; }
  .contact__address { font-weight: 500; font-size: 18px; line-height: 23px; margin-top: 18px; }
  .contact__list { list-style: none; margin-top: 14px; font-size: 18px; font-weight: 500; line-height: 23px; }
  .contact__list li { display: flex; align-items: center; gap: 10px; }
  .contact__list svg { width: 16px; height: 16px; fill: var(--orange); flex: none; }

  .back__brand {
    position: absolute; left: 0; right: 0; top: 160px;
    display: flex; justify-content: center;
  }
  .back__url {
    position: absolute; left: 0; right: 0; top: 378px;
    text-align: center; color: var(--white);
    font-size: 18px; font-weight: 500; letter-spacing: 3.6px;
  }
</style>
</head>
<body>
  <section class="card card--front">
    <div class="front__brand">
      <div class="wordmark wordmark--front">NORTHFIELD<br>BUILDERS GUILD</div>
    </div>
    <div class="front__divider"></div>
    <div class="front__details">
      <h1 class="contact__name">DANIEL REEVES</h1>
      <p class="contact__title">President</p>
      <p class="contact__address">2400 NW Cedar Ridge Rd.,<br>Suite #210<br>Millbrook, OR 97410</p>
      <ul class="contact__list">
        <li><svg viewBox="0 0 16 16"><path d="M3.5 1.5l2.5 0 1.2 3.2-1.6 1.2c.8 1.8 2.2 3.2 4 4l1.2-1.6 3.2 1.2v2.5c0 .8-.7 1.5-1.5 1.5C7 13.5 2 8.5 2 3c0-.8.7-1.5 1.5-1.5z"/></svg>(555) 014-2290</li>
        <li><svg viewBox="0 0 16 16"><path d="M4.5 1h7c.6 0 1 .4 1 1v12c0 .6-.4 1-1 1h-7c-.6 0-1-.4-1-1V2c0-.6.4-1 1-1zm1 2v9h5V3z"/></svg>555.013.7745</li>
        <li><svg viewBox="0 0 16 16"><path d="M1.5 4h13v8.5h-13zM2.5 5l5.5 4 5.5-4v1.3L8 10.3 2.5 6.3z"/></svg>support@nbguild.org</li>
        <li><svg viewBox="0 0 16 16"><circle cx="8" cy="8.5" r="6.5"/></svg>builderslinkguild.org</li>
      </ul>
    </div>
  </section>

  <section class="card card--back">
    <div class="back__brand">
      <div class="wordmark wordmark--back">NORTHFIELD<br>BUILDERS GUILD</div>
    </div>
    <p class="back__url">www.builderslinkguild.org</p>
  </section>
</body>
</html>
```